VOMRA Pty Ltd Business Card

Looking for a simple yet eye-catching double-sided business card design using my company logo on one side and contact details on the other.

Target Market(s)

Government

Industry/Entity Type

Communication Systems Engineering

Contact Information for Business Card

VOMRA Pty Ltd

Requirements
Nice to have
• Would be great to have a QR code so details can be scanned into contacts

```html
<!DOCTYPE html>
<html lang="en">
<head>
<meta charset="utf-8">
<title>VOMRA Pty Ltd Business Card</title>
<link href="https://fonts.googleapis.com/css2?family=Open+Sans:wght@400;600;700&display=swap" rel="stylesheet">
<style>
  :root {
    --backdrop: #2c2f33;
    --card: #ffffff;
    --ink: #37414a;
    --text: #1f2326;
  }
  * { margin: 0; padding: 0; box-sizing: border-box; }
  html, body { width: 1200px; height: 780px; overflow: hidden; }
  body {
    background: var(--backdrop);
    font-family: "Open Sans", sans-serif;
    display: flex;
    align-items: center;
    justify-content: center;
    gap: 44px;
  }
  .card {
    position: relative;
    width: 540px;
    height: 310px;
    background: var(--card);
    border-radius: 22px;
    overflow: hidden;
    box-shadow: 0 14px 30px rgba(0,0,0,0.45);
  }
  .card-wave { position: absolute; inset: 0; width: 100%; height: 100%; }
  .brand {
    position: absolute;
    display: flex;
    align-items: center;
    gap: 14px;
    color: var(--ink);
    font-weight: 700;
    letter-spacing: 0.04em;
    z-index: 1;
  }
  .brand-dot { border-radius: 50%; background: var(--ink); flex: none; }
  .front .brand { left: 30px; top: 22px; font-size: 46px; }
  .front .brand-dot { width: 40px; height: 40px; }
  .contact-list {
    position: absolute;
    left: 30px;
    top: 96px;
    list-style: none;
    font-size: 13px;
    line-height: 1.4;
    color: var(--text);
    z-index: 1;
  }
  .contact-list li { display: flex; align-items: center; gap: 7px; }
  .contact-list .address { display: block; margin-bottom: 2px; }
  .contact-icon { width: 11px; height: 11px; flex: none; }
  .person {
    position: absolute;
    right: 34px;
    top: 140px;
    text-align: right;
    color: var(--ink);
    z-index: 1;
  }
  .person-name { font-size: 28px; font-weight: 700; line-height: 1.1; }
  .person-role { font-size: 15px; color: var(--text); }
  .edge-tab {
    position: absolute;
    right: 0;
    top: 226px;
    width: 34px;
    height: 30px;
    background: var(--ink);
  }
  .back { display: flex; align-items: center; justify-content: center; }
  .back .brand { position: static; font-size: 78px; gap: 22px; }
  .back .brand-dot { width: 62px; height: 62px; }
</style>
</head>
<body>
  <section class="card front" aria-label="Contact side">
    <svg class="card-wave" viewBox="0 0 540 310" preserveAspectRatio="none" aria-hidden="true">
      <path d="M0 215 C40 245 100 262 180 270 C270 278 330 284 380 310 L0 310 Z" fill="#37414a"/>
      <path d="M14 228 C40 252 72 266 112 276" fill="none" stroke="#ffffff" stroke-width="3" stroke-linecap="round"/>
      <path d="M380 310 C420 296 460 290 500 288 L540 288 L540 310 Z" fill="#37414a"/>
    </svg>
    <div class="brand"><span class="brand-dot"></span><span class="brand-name">VOMRA</span></div>
    <ul class="contact-list">
      <li class="address">14-16 Harbour Lane Redfern<br>NSW 2016 Australia</li>
      <li>
        <svg class="contact-icon" viewBox="0 0 12 12" aria-hidden="true"><path d="M2.5 1 L4.5 1 L5.3 3.6 L4 4.6 C4.6 6 5.8 7.3 7.3 8 L8.4 6.7 L11 7.5 L11 9.5 C11 10.4 10.3 11 9.5 11 C5 10.7 1.3 7 1 2.5 C1 1.7 1.6 1 2.5 1 Z" fill="#37414a"/></svg>
        (555) 014-3926
      </li>
      <li>
        <svg class="contact-icon" viewBox="0 0 12 12" aria-hidden="true"><circle cx="6" cy="6" r="5" fill="none" stroke="#37414a" stroke-width="1.4"/><path d="M1 6 H11 M6 1 C3.5 4 3.5 8 6 11 M6 1 C8.5 4 8.5 8 6 11" fill="none" stroke="#37414a" stroke-width="1"/></svg>
        www.vomra.com.au
      </li>
      <li>
        <svg class="contact-icon" viewBox="0 0 12 12" aria-hidden="true"><rect x="1" y="2.5" width="10" height="7" rx="1" fill="none" stroke="#37414a" stroke-width="1.4"/><path d="M1.5 3 L6 6.6 L10.5 3" fill="none" stroke="#37414a" stroke-width="1.2"/></svg>
        admin@vomra.com.au
      </li>
    </ul>
    <div class="person">
      <p class="person-name">Mara Jennings</p>
      <p class="person-role">Co-Founder</p>
    </div>
    <div class="edge-tab"></div>
  </section>

  <section class="card back" aria-label="Logo side">
    <div class="brand"><span class="brand-dot"></span><span class="brand-name">VOMRA</span></div>
  </section>
</body>
</html>
```